Pinecrest Harbor Foundation Web Design

The design we need is for a WordPress blog that will be our content platform. We are a registered 501(c)3 non-profit that focuses on financially supporting the treatment of cancer patients that have been told they have no hope and there is nothing the conventional medical system can do for them. Through this wesbite we want to both rasie awareness about the treatment options plus, raise funds for treating patients. The two primary target audiences of the site are...

1. Terminally ill patients and their families to let them know that there is an option other then hospice and that we are hear to support that option.

2. People looking to help donate to a worthwhile cause that resonates with them.

The website is https://pinecrestharborfoundation.org/

See attached logo designs!!!

Target Market(s)

Cancer patients and their families

Industry/Entity Type

Foundation

Font styles to use
Sans Serif

Colors
ffffff
fbed22

Requirements
Must have
• I like this look of this site. It is clean, simple, helpful, soft. I like the flow of the pages.
• http://www.meadowsforcalm.org/
• I like the design and flow but NOT the color or boldness
• https://tvbn-youth.org/
• I like this style for a donation page.
• https://www.tumorstudyhub.org/we-are-tsh/join-the-cause/donations/one-time-donation
• with the addition of a Would you like your employer to match? button.
Nice to have
• White black and gold - but soft
• Even possibly grayscale like the site I like.

```html
<!DOCTYPE html>
<html lang="en">
<head>
<meta charset="utf-8">
<title>Pinecrest Harbor Foundation</title>
<link href="https://fonts.googleapis.com/css2?family=Montserrat:wght@400;500;600;700&family=Open+Sans:wght@400;600&display=swap" rel="stylesheet">
<style>
:root{
  --orange:#f7830e;
  --orange-dark:#e8750a;
  --dark:#2e2e2e;
  --footer:#2b2b2b;
  --text:#333333;
  --muted:#7a7a7a;
  --light:#f4f5f7;
  --line:#e3e3e3;
  --white:#ffffff;
}
*{box-sizing:border-box;margin:0;padding:0}
html,body{width:1200px;height:3041px;overflow:hidden}
body{font-family:"Open Sans",Arial,sans-serif;color:var(--text);background:var(--white);position:relative}
.wrap{position:absolute;inset:0}
h1,h2,h3,h4,.nav a,.btn{font-family:"Montserrat",Arial,sans-serif}

/* header */
.site-header{position:absolute;top:0;left:0;width:1200px;height:101px;border-top:4px solid var(--orange);background:var(--white)}
.brand{position:absolute;left:88px;top:22px;text-align:center;width:240px}
.brand-name{font-family:"Montserrat",sans-serif;font-weight:700;color:var(--orange);font-size:19px;letter-spacing:.3px}
.brand-sub{font-family:"Montserrat",sans-serif;font-weight:600;font-size:12px;letter-spacing:4px;color:var(--dark);border-top:1px solid var(--line);margin-top:8px;padding-top:7px}
.nav{position:absolute;right:86px;top:44px;display:flex;gap:42px}
.nav a{font-size:11.5px;font-weight:600;color:var(--dark);text-decoration:none;letter-spacing:.3px}
.nav a.active{color:var(--orange)}

/* hero */
.hero{position:absolute;top:101px;left:0;width:1200px;height:517px;background:linear-gradient(100deg,#5c6064 0%,#8f8a86 45%,#b7aaa0 70%,#6f6863 100%)}
.hero-overlay{position:absolute;inset:0;background:rgba(30,30,30,.35)}
.hero-content{position:absolute;top:170px;left:0;width:1200px;text-align:center;color:var(--white)}
.hero-content h1{font-size:32px;font-weight:700;letter-spacing:.5px}
.hero-content p{font-size:12px;line-height:29px;margin:14px auto 0;width:700px}
.btn{display:inline-block;font-weight:600;text-transform:uppercase;text-decoration:none}
.btn-orange{background:var(--orange);color:var(--white);font-size:14px;padding:13px 20px;margin-top:24px;border-radius:2px}
.dots{position:absolute;bottom:38px;left:0;width:1200px;display:flex;justify-content:center;gap:10px}
.dots span{width:16px;height:16px;border:2px solid var(--white);border-radius:50%}
.dots span.on{border-color:var(--orange)}

/* features */
.features{position:absolute;top:618px;left:0;width:1200px;height:114px;display:flex}
.feature{flex:1;display:flex;align-items:center;padding-left:85px;color:var(--white)}
.feature.orange{background:var(--orange)}
.feature.dark{background:var(--dark);padding-left:15px}
.feature-icon{width:93px;height:93px;border-radius:50%;background:var(--white);display:flex;align-items:center;justify-content:center;flex:none}
.feature-text{margin-left:20px}
.feature-text h3{font-size:13px;font-weight:600;letter-spacing:.2px}
.feature-text p{font-size:10.5px;margin-top:14px}

/* welcome */
.welcome{position:absolute;top:732px;left:0;width:1200px;height:446px}
.welcome-photo{position:absolute;left:85px;top:71px;width:463px;height:313px;background:linear-gradient(135deg,#c7d6de,#8ba3b3 50%,#d4b5b0)}
.welcome-text{position:absolute;left:600px;top:85px;width:460px}
.welcome-text h2{font-size:16px;font-weight:700;color:var(--dark)}
.welcome-text h4{font-size:15px;font-weight:600;color:var(--orange);line-height:27px;margin-top:16px;text-transform:uppercase}
.welcome-text p{font-size:11px;line-height:25px;color:var(--muted);margin-top:16px}

/* section heads */
.section-head h2{font-size:21px;font-weight:700;color:var(--dark);text-transform:uppercase}
.section-head h2 span{font-weight:400}
.section-head p{font-size:10.5px;color:var(--muted);margin-top:9px}

/* causes */
.causes{position:absolute;top:1178px;left:0;width:1200px;height:542px;background:var(--light)}
.causes .section-head{position:absolute;left:85px;top:30px}
.arrows{position:absolute;right:86px;top:26px;display:flex;gap:4px}
.arrows span{width:30px;height:30px;border:1.5px solid #a9a9a9;border-radius:50%;display:flex;align-items:center;justify-content:center}
.cards{position:absolute;left:85px;top:110px;display:flex;gap:12px}
.card{width:248px;height:372px;background:var(--white);box-shadow:0 1px 3px rgba(0,0,0,.08)}
.card-photo{height:182px}
.c1{background:linear-gradient(135deg,#dfe8ee,#9db6c6)}
.c2{background:linear-gradient(135deg,#8aa0b5,#3a4756)}
.c3{background:linear-gradient(135deg,#d9dde2,#93a3b0)}
.c4{background:linear-gradient(135deg,#f0e2d8,#c7a694)}
.card-body{padding:20px 15px}
.card-body h3{font-size:12px;font-weight:600;color:var(--dark)}
.card-body p{font-size:10.5px;line-height:24px;color:var(--muted);margin-top:10px}
.progress{position:relative;margin-top:30px;height:12px;background:#dedee3;border-radius:6px}
.progress .fill{position:absolute;left:0;top:0;height:12px;width:50%;border-radius:6px;background:repeating-linear-gradient(135deg,var(--orange) 0 6px,#fbab5b 6px 9px)}
.progress .pct{position:absolute;left:calc(50% - 34px);top:-20px;background:var(--orange);color:var(--white);font-size:9px;font-weight:600;padding:2px 5px}

/* nonprofit band */
.nonprofit{position:absolute;top:1720px;left:0;width:1200px;height:368px;background:linear-gradient(90deg,var(--orange),var(--orange-dark))}
.np-text{position:absolute;left:85px;top:82px;width:450px;color:var(--white)}
.np-text h2{font-size:27px;font-weight:600}
.np-text p{font-size:10.5px;line-height:24px;margin-top:14px}
.btn-outline{border:1.5px solid var(--white);color:var(--white);font-size:13px;padding:14px 32px;margin-top:34px}
.stats{position:absolute;left:588px;top:82px;display:flex;gap:75px}
.stat{width:110px;text-align:center;color:var(--white)}
.stat-circle{width:110px;height:110px;border:3px solid var(--white);border-radius:50%;display:flex;align-items:center;justify-content:center}
.stat h4{font-family:"Montserrat",sans-serif;font-size:10px;font-weight:600;margin-top:28px;white-space:nowrap;margin-left:-20px;margin-right:-20px}
.stat strong{display:block;font-family:"Montserrat",sans-serif;font-size:17px;font-weight:500;margin-top:6px}

/* news */
.news{position:absolute;top:2088px;left:0;width:1200px;height:512px}
.news .section-head{position:absolute;left:85px;top:31px}
.posts{position:absolute;left:85px;top:109px;display:flex;gap:13px}
.post{width:335px}
.post-photo{position:relative;height:211px}
.n1{background:linear-gradient(135deg,#c9d2cf,#8d9a98 60%,#d8c3b4)}
.n2{background:linear-gradient(135deg,#8e8d8c,#c8b9a8 55%,#574c45)}
.n3{background:linear-gradient(135deg,#9fb88a,#5f7a4c 60%,#c7d4b7)}
.date{position:absolute;right:15px;bottom:-28px;width:70px;height:71px;background:var(--orange);color:var(--white);text-align:center;font-family:"Montserrat",sans-serif}
.date b{display:block;font-size:22px;font-weight:600;padding-top:6px}
.date span{display:block;font-size:14px;border-top:1px solid rgba(255,255,255,.7);margin:4px 10px 0;padding-top:4px}
.post h3{font-size:16px;font-weight:600;color:var(--dark);margin-top:32px}
.post p{font-size:10.5px;line-height:25px;color:var(--muted);margin-top:12px}

/* partners */
.partners{position:absolute;top:2600px;left:0;width:1200px;height:205px;background:var(--light)}
.partner-row{position:absolute;left:104px;top:52px;display:flex;gap:30px}
.partner{width:175px;height:98px;background:var(--white);display:flex;align-items:center;justify-content:center;font-family:"Montserrat",sans-serif;font-size:22px;font-weight:500;color:#9a9a9a}
.side-arrow{position:absolute;top:75px}

/* footer */
.site-footer{position:absolute;top:2805px;left:0;width:1200px;height:236px;background:var(--footer);color:var(--white)}
.social{position:absolute;top:32px;left:0;width:1200px;display:flex;justify-content:center;gap:14px}
.social span{width:60px;height:60px;border:1.5px solid rgba(255,255,255,.85);border-radius:50%;display:flex;align-items:center;justify-content:center}
.footer-rule{position:absolute;top:107px;left:85px;width:1030px;border-top:1px solid #3d3d3d}
.footer-nav{position:absolute;top:129px;left:0;width:1200px;display:flex;justify-content:center;font-family:"Montserrat",sans-serif;font-size:11px;font-weight:500}
.footer-nav a{color:var(--white);text-decoration:none;padding:0 22px;border-right:1px solid #bbb;line-height:11px}
.footer-nav a:last-child{border-right:none}
.copyright{position:absolute;top:175px;left:0;width:1200px;text-align:center;font-size:11px}
</style>
</head>
<body>
<div class="wrap">

<header class="site-header">
  <div class="brand">
    <div class="brand-name">PINECREST HARBOR</div>
    <div class="brand-sub">FOUNDATION</div>
  </div>
  <nav class="nav">
    <a class="active" href="#">HOME</a>
    <a href="#">ABOUT US</a>
    <a href="#">SERVICES</a>
    <a href="#">SPONSORSHIP</a>
    <a href="#">NEWS</a>
    <a href="#">CONTACT US</a>
  </nav>
</header>

<section class="hero" role="img" aria-label="Photo of a smiling woman embracing a patient wearing a headscarf">
  <div class="hero-overlay"></div>
  <div class="hero-content">
    <h1>PINECREST HARBOR FOUNDATION</h1>
    <p>Sed ut perspiciatis unde omnis iste natus error sit voluptatem accusantium doloremque laudantium, totam rem aperiam, quae ab illo inventore veritatis et quasi architecto beatae vitae dicta sunt explicabo.</p>
    <a class="btn btn-orange" href="#">READ MORE</a>
  </div>
  <div class="dots"><span></span><span class="on"></span><span></span></div>
</section>

<section class="features">
  <div class="feature orange">
    <div class="feature-icon">
      <svg width="40" height="56" viewBox="0 0 40 56"><path d="M20 4c-8 0-11 8-7 17l-10 27 8 4 9-22 9 22 8-4-10-27c4-9 1-17-7-17zm0 7c3 0 4 4 2 9l-2 4-2-4c-2-5-1-9 2-9z" fill="#f7830e"/></svg>
    </div>
    <div class="feature-text">
      <h3>ABOUT CANCER PATIENTS</h3>
      <p>Sed ut perspiciatis unde omnis iste natus error sit voluptatem</p>
    </div>
  </div>
  <div class="feature dark">
    <div class="feature-icon">
      <svg width="52" height="52" viewBox="0 0 52 52" fill="#2e2e2e"><circle cx="20" cy="8" r="6"/><path d="M14 16h12v16h10l6 14h-5l-5-10H14z"/><circle cx="40" cy="20" r="4"/><path d="M37 26h6v22h-6z"/><path d="M10 26a14 14 0 1 0 14 22h-6a9 9 0 1 1-8-15z"/></svg>
    </div>
    <div class="feature-text">
      <h3>RAISE FUNDS FOR TREATING PATIENTS</h3>
      <p>Sed ut perspiciatis unde omnis iste natus error sit voluptatem</p>
    </div>
  </div>
</section>

<section class="welcome">
  <div class="welcome-photo" role="img" aria-label="Photo of a person holding an awareness ribbon to their chest"></div>
  <div class="welcome-text">
    <h2>WELCOME TO PINECREST HARBOR FOUNDATION</h2>
    <h4>People looking to help donate to a worthwhile cause that resonates with them.</h4>
    <p>Sed ut perspiciatis unde omnis iste natus error sit voluptatem accusantium doloremque laudantium, totam rem aperiam, eaque ipsa quae ab illo inventore veritatis et quasi architecto beatae vitae dicta sunt explicabo. Nemo enim ipsam voluptatem quia voluptas sit aspernatur aut odit aut fugit, sed quia consequuntur magni dolores eos qui ratione voluptatem sequi nesciunt.</p>
    <p>Sed ut perspiciatis unde omnis iste natus error sit voluptatem accusantium doloremque laudantium, totam rem aperiam, eaque ipsa quae ab illo inventore veritatis et quasi architecto beatae vitae dicta sunt explicabo.</p>
  </div>
</section>

<section class="causes">
  <div class="section-head">
    <h2>RECENT <span>CAUSES</span></h2>
    <p>Sed ut perspiciatis unde omnis iste natus error sit voluptatem accusantium doloremque laudantium, totam rem aperiam</p>
  </div>
  <div class="arrows">
    <span><svg width="10" height="10" viewBox="0 0 10 10"><path d="M7 1L3 5l4 4" stroke="#888" stroke-width="1.5" fill="none"/></svg></span>
    <span><svg width="10" height="10" viewBox="0 0 10 10"><path d="M3 1l4 4-4 4" stroke="#888" stroke-width="1.5" fill="none"/></svg></span>
  </div>
  <div class="cards">
    <article class="card"><div class="card-photo c1" role="img" aria-label="Photo of a doctor with a patient in a hospital bed"></div><div class="card-body"><h3>SED UT PERSPICIATIS UNDE</h3><p>Sed ut perspiciatis unde omnis iste nat us error sit voluptatem accusantium dol oremque laudantium, totam</p><div class="progress"><div class="fill"></div><span class="pct">50%</span></div></div></article>
    <article class="card"><div class="card-photo c2" role="img" aria-label="Photo of a patient receiving treatment"></div><div class="card-body"><h3>SED UT PERSPICIATIS UNDE</h3><p>Sed ut perspiciatis unde omnis iste nat us error sit voluptatem accusantium dol oremque laudantium, totam</p><div class="progress"><div class="fill"></div><span class="pct">50%</span></div></div></article>
    <article class="card"><div class="card-photo c3" role="img" aria-label="Photo of a smiling doctor with a stethoscope"></div><div class="card-body"><h3>SED UT PERSPICIATIS UNDE</h3><p>Sed ut perspiciatis unde omnis iste nat us error sit voluptatem accusantium dol oremque laudantium, totam</p><div class="progress"><div class="fill"></div><span class="pct">50%</span></div></div></article>
    <article class="card"><div class="card-photo c4" role="img" aria-label="Photo of a nurse with an elderly patient"></div><div class="card-body"><h3>SED UT PERSPICIATIS UNDE</h3><p>Sed ut perspiciatis unde omnis iste nat us error sit voluptatem accusantium dol oremque laudantium, totam</p><div class="progress"><div class="fill"></div><span class="pct">50%</span></div></div></article>
  </div>
</section>

<section class="nonprofit">
  <div class="np-text">
    <h2>NON PROFIT ORGANISATION</h2>
    <p>Sed ut perspiciatis unde omnis iste natus error sit voluptatem accusantium doloremque laudantium, totam rem aperiam, eaque ipsa quae ab illo inventore veritatis et quasi architecto beatae vitae dicta sunt explicabo.</p>
    <a class="btn btn-outline" href="#">DONATE NOW!</a>
  </div>
  <div class="stats">
    <div class="stat"><div class="stat-circle"><svg width="24" height="36" viewBox="0 0 24 36"><text x="12" y="29" text-anchor="middle" font-family="Montserrat,sans-serif" font-size="32" font-weight="600" fill="#fff">$</text></svg></div><h4>SED UT PERSPICIATIS UNDE</h4><strong>$ 20000</strong></div>
    <div class="stat"><div class="stat-circle"><svg width="40" height="30" viewBox="0 0 40 30" fill="#fff"><path d="M20 2L0 11l20 9 20-9z"/><path d="M8 16v7c0 3 6 5 12 5s12-2 12-5v-7l-12 6z"/><rect x="35" y="11" width="2" height="12"/></svg></div><h4>SED UT PERSPICIATIS</h4><strong>$ 10</strong></div>
    <div class="stat"><div class="stat-circle"><svg width="36" height="28" viewBox="0 0 36 28" fill="#fff"><circle cx="18" cy="7" r="6"/><circle cx="7" cy="10" r="4.5"/><circle cx="29" cy="10" r="4.5"/><path d="M8 27c0-8 4-12 10-12s10 4 10 12z"/><path d="M0 26c0-6 3-9 7-9 2 0 3 .5 4 1.5C9 20 8 23 7 26z"/><path d="M36 26c0-6-3-9-7-9-2 0-3 .5-4 1.5 2 1.5 3 4.5 4 7.5z"/></svg></div><h4>SED UT PERSPICIATIS</h4><strong>$ 5000</strong></div>
  </div>
</section>

<section class="news">
  <div class="section-head">
    <h2>LATEST <span>NEWS</span></h2>
    <p>Sed ut perspiciatis unde omnis iste natus error sit voluptatem accusantium doloremque laudantium, totam rem aperiam</p>
  </div>
  <div class="posts">
    <article class="post"><div class="post-photo n1" role="img" aria-label="Photo of a patient and a young woman embracing"><div class="date"><b>25</b><span>NOV</span></div></div><h3>SED UT PERSPICIATIS</h3><p>Sed ut perspiciatis unde omnis iste natus error sit volupta tem accusantium doloremque laudantium, totamrem quasi architecto beatae vitae dicta sunt explicabo</p></article>
    <article class="post"><div class="post-photo n2" role="img" aria-label="Photo of a patient resting in a hospital bed"><div class="date"><b>25</b><span>NOV</span></div></div><h3>SED UT PERSPICIATIS</h3><p>Sed ut perspiciatis unde omnis iste natus error sit volupta tem accusantium doloremque laudantium, totamrem quasi architecto beatae vitae dicta sunt explicabo</p></article>
    <article class="post"><div class="post-photo n3" role="img" aria-label="Photo of two people hugging outdoors"><div class="date"><b>25</b><span>NOV</span></div></div><h3>SED UT PERSPICIATIS</h3><p>Sed ut perspiciatis unde omnis iste natus error sit volupta tem accusantium doloremque laudantium, totamrem quasi architecto beatae vitae dicta sunt explicabo</p></article>
  </div>
</section>

<section class="partners">
  <svg class="side-arrow" style="left:48px" width="16" height="50" viewBox="0 0 16 50"><path d="M14 2L3 25l11 23" stroke="#d5d5d5" stroke-width="2" fill="none"/></svg>
  <div class="partner-row">
    <div class="partner">Kestrel</div>
    <div class="partner">Lumora</div>
    <div class="partner">Brightfold</div>
    <div class="partner">Openfield</div>
    <div class="partner">Northvane</div>
  </div>
  <svg class="side-arrow" style="right:48px" width="16" height="50" viewBox="0 0 16 50"><path d="M2 2l11 23L2 48" stroke="#d5d5d5" stroke-width="2" fill="none"/></svg>
</section>

<footer class="site-footer">
  <div class="social">
    <span aria-label="Social profile 1"></span>
    <span aria-label="Social profile 2"></span>
    <span aria-label="Social profile 3"></span>
    <span aria-label="Social profile 4"></span>
    <span aria-label="Social profile 5"></span>
    <span aria-label="Email"><svg width="18" height="14" viewBox="0 0 18 14"><rect x="1" y="1" width="16" height="12" rx="1" stroke="#fff" stroke-width="1.5" fill="none"/><path d="M1 2l8 6 8-6" stroke="#fff" stroke-width="1.5" fill="none"/></svg></span>
  </div>
  <div class="footer-rule"></div>
  <nav class="footer-nav">
    <a href="#">HOME</a><a href="#">ABOUT US</a><a href="#">SERVICES</a><a href="#">SPONSORSHIP</a><a href="#">NEWS</a><a href="#">CONTACT US</a>
  </nav>
  <p class="copyright">© Copyrights 2017 Pinecrest Harbor Foundation.All Rights Reserved.</p>
</footer>

</div>
</body>
</html>
```